Business Card Design

Hi I need a business card designed, we already have the business name logo artwork and would like some concept ideas for the Bus Card layout.
On the back of the card i want to include the products and services that we offer.
We are a Plastics Sheeting manufacture based in Perth Australia.

                                       

We need a BC design for a company called Tarvo Plastics based in Perth Australia.

We supply from DIY to Trade & Industrial  Engineering Markets.

We specialise in:

·         Cut to size panels  (all shapes and sizes)

·         Plastics fabrication & Welding

·         Custom Designs

·         Plastic Repairs

·         PVC Pipe Slotting & PVC Pipe Threading

·         Supplier of all types of engineering plastics and profiles.

Including:           Acrylic / Clarvene

                               Polycarbonate / Dorvil

                               Prismatic Light Diffuser

                               Vantrib

                               HDPE / UHMWPE

                               PVC / PVC Foam

                               Nylon

                               HIPS

```html
<!DOCTYPE html>
<html lang="en">
<head>
<meta charset="utf-8">
<title>Tarvo Plastics – Business Card</title>
<link rel="stylesheet" href="https://fonts.googleapis.com/css2?family=Open+Sans:ital,wght@0,400;0,600;0,700;0,800;1,700&display=swap">
<style>
  :root {
    --navy: #1b2a5c;
    --grey-text: #555a63;
    --orange: #e8781e;
    --rule: #b9bcc2;
    --card: #ffffff;
    --backdrop: #e4e5ea;
  }
  * { box-sizing: border-box; margin: 0; padding: 0; }
  html, body {
    width: 1200px; height: 987px; overflow: hidden;
    background: var(--backdrop);
    font-family: "Open Sans", Arial, sans-serif;
  }
  .stage {
    position: relative; width: 1200px; height: 987px;
    display: flex; flex-direction: column; align-items: center; justify-content: center; gap: 34px;
  }
  .card {
    position: relative; width: 800px; height: 457px;
    background: var(--card); border-radius: 34px; overflow: hidden;
    box-shadow: 0 6px 18px rgba(0,0,0,.12);
  }

  /* Front */
  .brand-name {
    position: absolute; left: 150px; top: 60px;
    font-size: 70px; font-weight: 800; color: var(--navy); letter-spacing: -1px; line-height: 1;
  }
  .divider {
    position: absolute; left: 0; right: 0; top: 246px; height: 3px;
    background: linear-gradient(90deg, rgba(185,188,194,0) 0%, var(--rule) 40%, #9a9ea6 100%);
  }
  .contact-list {
    position: absolute; left: 40px; top: 268px; list-style: none;
    font-size: 19px; color: var(--grey-text); line-height: 1.45;
  }
  .contact-list li { display: flex; align-items: center; gap: 8px; }
  .contact-list svg { width: 15px; height: 15px; fill: var(--navy); flex: none; }
  .person {
    position: absolute; right: 46px; top: 166px; text-align: right;
  }
  .person-name { font-size: 30px; font-weight: 700; color: var(--navy); line-height: 1.1; }
  .person-title { font-size: 21px; color: var(--orange); margin-top: 4px; line-height: 1.2; }
  .address {
    position: absolute; right: 46px; top: 268px; text-align: right; font-style: normal;
    font-size: 21px; color: var(--grey-text); line-height: 1.3;
  }
  .address p + p { margin-top: 16px; }

  /* Back */
  .back { padding: 34px 40px 0; text-align: center; color: var(--grey-text); }
  .tagline {
    font-size: 21px; font-weight: 700; font-style: italic; color: var(--navy); line-height: 1.25;
  }
  .section-head {
    font-size: 25px; font-weight: 700; color: var(--navy); margin-top: 18px; line-height: 1.2;
  }
  .offer-list {
    list-style: none; font-size: 18px; line-height: 1.4; margin-top: 4px;
  }
  .offer-list li { display: inline; }
  .offer-list li::before { content: "• "; color: #2a6fb8; }
  .offer-list li + li { margin-left: 10px; }
  .offer-list .break { display: block; height: 0; }
</style>
</head>
<body>
<main class="stage">

  <section class="card card-front" aria-label="Card front">
    <div class="brand-name">Tarvo Plastics</div>

    <div class="person">
      <div class="person-name">Your Name</div>
      <div class="person-title">Title</div>
    </div>

    <div class="divider"></div>

    <ul class="contact-list">
      <li><svg viewBox="0 0 16 16"><path d="M3.5 1l2.5 3-1.5 1.6c.8 2 2.4 3.6 4.4 4.4L10.5 8.5l3 2.5-1.5 2.8C6.5 13.5 2.5 9.5 1 4.2z"/></svg>08 9000 4127</li>
      <li><svg viewBox="0 0 16 16"><path d="M4.5 0h7a1 1 0 011 1v14a1 1 0 01-1 1h-7a1 1 0 01-1-1V1a1 1 0 011-1zm.5 2v10h6V2zm3 11a1 1 0 100 2 1 1 0 000-2z"/></svg>0400 555 718</li>
      <li><svg viewBox="0 0 16 16"><path d="M4 1h7v4H4zM2 6h12a1 1 0 011 1v6a1 1 0 01-1 1H2a1 1 0 01-1-1V7a1 1 0 011-1zm2 5h8v-1H4z"/></svg>08 9000 4128</li>
      <li><svg viewBox="0 0 16 16"><path d="M1 3h14v10H1zm1.5 1.3V5l5.5 4 5.5-4v-.7L8 8.2z"/></svg>sales@tarvoplastics.com.au</li>
    </ul>

    <address class="address">
      <p>Unit 4/18 Marlow Crescent<br>Bexley Vale WA 6193</p>
      <p>PO Box 2741<br>Bexley Vale DC WA 6987</p>
    </address>
  </section>

  <section class="card card-back back" aria-label="Card back">
    <p class="tagline">The Products And Services That We Offer<br>Are Supplied From Diy To Trade &amp; Industrial Engineering Markets</p>

    <h2 class="section-head">We specialise in:</h2>
    <ul class="offer-list">
      <li>Cut to size panels (all shapes and sizes)</li>
      <span class="break"></span>
      <li>Plastics fabrication &amp; Welding</li><li>Custom Designs</li>
      <span class="break"></span>
      <li>Plastic Repairs</li><li>PVC Pipe Slotting &amp; PVC Pipe Threading</li>
      <span class="break"></span>
      <li>Supplier of all types of engineering plastics and profiles</li>
    </ul>

    <h2 class="section-head">Including:</h2>
    <ul class="offer-list">
      <li>Acrylic / Clarvene</li><li>Polycarbonate / Dorvil</li>
      <span class="break"></span>
      <li>Prismatic Light Diffuser</li><li>Vantrib</li><li>HDPE / UHMWPE</li>
      <span class="break"></span>
      <li>PVC / PVC Foam</li><li>Nylon</li><li>HIPS</li>
    </ul>
  </section>

</main>
</body>
</html>
```